Website redesign for Halt and Fullmane

We would like to update the design of our current website to a more concise, conversion optimized design.
The goal of our website is to get our message across as concisely as possible plus encourage people to contact us for more information or to book a consultation.
We need a redesign of the home page and 1 internal page - just for design/layout purposes/format purposes.

Target Market(s)

Males 20-45 years old who are concerned about hair loss and who want to regrow their own hair.

Industry/Entity Type

Health And Wellness

Number of Pages Required

2 page

Font styles to use
Sans Serif

Colors
00a990
33a6d7
ffffff
9d9d9d

Requirements
Must have
• We want the home page to be very concise and to the point in getting the message across. We want to get across the following 6 key messages:
• 1. Dr Pembrook story – why he created this solution
• 2. Hair loss is caused by a chemical imbalance
• 3. Halt and fullmane conducts genetic and DNA analysis, then rebalances body chemistry, thus reversing the hair loss process and enabling your own hair to regrow naturally
• 4. Money back guaranteed results
• 5. Purely Core ingredients – no harsh preservatives or chemicals are included
• 6. All ingredients are FDA approved and safe – no side effects
• We also need a strong call to action. We want people to call or email us to find out more information or to schedule a consultation.
• Here is our current website which is not performing as we would hope: http://www.haltandfullmane.example/
• Here is our press release for further information: https://www.pressdeskhub.example/news/finally-we-now-have-a-cure-for-male-pattern-baldness-28461902
• I uploaded the logo files, but let me know if anything else is needed and I can add it.

```html
<!DOCTYPE html>
<html lang="en">
<head>
<meta charset="utf-8">
<title>Halt and Fullmane – Home</title>
<link rel="stylesheet" href="https://fonts.googleapis.com/css2?family=Raleway:wght@400;500;600;700;800&family=Exo+2:wght@500;600;700&family=Open+Sans:wght@400;600&display=swap">
<style>
:root{
  --green:#00a990;
  --blue:#33a6d7;
  --white:#ffffff;
  --grey:#9d9d9d;
  --ink:#4a4a4a;
  --dark:#222222;
  --footer:#262626;
  --rule:#3a3a3a;
}
*{box-sizing:border-box;margin:0;padding:0}
html,body{width:1200px;height:2479px;overflow:hidden;background:var(--white)}
body{font-family:"Raleway",sans-serif;color:var(--ink);position:relative}
.block{position:absolute;left:0;width:1200px}
.btn{display:inline-flex;align-items:center;justify-content:center;color:var(--white);font-size:13px;font-weight:600;text-decoration:none}

/* header */
.site-header{top:0;height:102px}
.brand{position:absolute;left:99px;top:20px;display:flex;align-items:center;gap:12px}
.brand-mark{width:50px;height:50px;border-radius:50%;background:var(--green)}
.brand-name{font-size:30px;font-weight:500;color:#555;line-height:1}
.brand-by{position:absolute;left:258px;top:62px;font-size:17px;font-weight:500;color:var(--blue)}
.call{position:absolute;left:683px;top:22px;display:flex;align-items:center;gap:14px}
.call-label{font-size:10px;font-weight:600;color:#666;letter-spacing:.5px}
.call-number{font-size:23px;font-weight:700;color:var(--dark)}
.header-cta{position:absolute;left:926px;top:25px;width:175px;height:43px;background:var(--green);font-size:12px}

/* nav */
.main-nav{top:102px;height:45px;background:var(--blue)}
.main-nav ul{list-style:none;display:flex;position:absolute;left:112px;top:0;height:45px;align-items:center;gap:30px}
.main-nav a{color:var(--white);font-size:14px;font-weight:500;text-decoration:none}
.nav-search{position:absolute;left:1053px;top:0;width:48px;height:45px;background:var(--green);display:flex;align-items:center;justify-content:center}

/* hero */
.hero{top:147px;height:498px;background:linear-gradient(90deg,#eceef0 0%,#e6eaed 45%,#cfd8de 70%,#b9c4cc 100%)}
.hero-photo{position:absolute;left:520px;top:0;width:680px;height:498px;background:radial-gradient(ellipse at 60% 50%,#d8c2b0 0%,#c9b4a3 25%,rgba(200,210,218,0) 60%)}
.hero-title{position:absolute;left:101px;top:135px;width:490px;font-size:28px;font-weight:500;line-height:1.3;color:var(--blue)}
.hero-text{position:absolute;left:101px;top:228px;width:390px;font-size:16px;line-height:1.4;color:#444}
.hero-actions{position:absolute;left:101px;top:304px;display:flex;gap:7px}
.hero-actions .btn{height:45px}
.btn-blue{background:var(--blue);width:121px}
.btn-green{background:var(--green);width:121px}

/* about */
.about{top:645px;height:400px}
.section-title{font-size:31px;font-weight:700;color:#444;letter-spacing:.3px}
.about .section-title{position:absolute;left:102px;top:52px;border-bottom:3px solid var(--ink);padding-bottom:2px}
.about-sub{position:absolute;left:102px;top:108px;font-size:18px;font-weight:600;color:var(--blue)}
.about-text{position:absolute;left:102px;top:143px;width:492px;font-size:12px;line-height:17.4px;color:#333;text-align:justify}
.about .btn{position:absolute;left:104px;top:284px;width:122px;height:45px;background:var(--blue)}
.about-video{position:absolute;left:622px;top:59px;width:479px;height:294px;background:linear-gradient(120deg,#8f7a6a 0%,#c4a995 40%,#a08a7a 70%,#6f6258 100%)}
.play{position:absolute;left:50%;top:50%;transform:translate(-50%,-50%)}

/* how it works */
.how{top:1046px;height:414px}
.how-photo{position:absolute;left:0;top:0;width:597px;height:414px;background:linear-gradient(135deg,#e6e4e0 0%,#c7b6a6 45%,#6fb9a6 70%,#3d3b3a 100%)}
.how-panel{position:absolute;left:597px;top:0;width:603px;height:414px;background:var(--green);color:var(--white)}
.how-panel .section-title{position:absolute;left:26px;top:28px;color:var(--white);font-size:29px;border-bottom:2px solid var(--white);padding-bottom:2px}
.how-sub{position:absolute;left:28px;top:100px;font-size:16.5px;font-weight:700;line-height:1.3}
.how-text{position:absolute;left:28px;top:148px;width:510px;font-size:12.2px;line-height:1.72}
.how-text p+p{margin-top:20px}
.how-more{position:absolute;left:28px;top:333px;font-size:14px}

/* why */
.why{top:1460px;height:527px}
.why-title{position:absolute;left:0;width:1200px;top:58px;text-align:center;font-size:29px;font-weight:700;color:#555}
.why-title::after{content:"";position:absolute;left:548px;top:36px;width:102px;height:2px;background:var(--ink)}
.features{position:absolute;left:104px;top:133px;display:flex;gap:26px}
.feature{width:311px;text-align:center}
.feature-photo{height:230px}
.feature:nth-child(1) .feature-photo{background:linear-gradient(135deg,#9c8473,#d5bba6 50%,#e8e2dc)}
.feature:nth-child(2) .feature-photo{background:linear-gradient(135deg,#e7e9ea,#c9ad98 55%,#8c7564)}
.feature:nth-child(3) .feature-photo{background:linear-gradient(135deg,#dfe5e9,#cdb19c 55%,#b7c2c9)}
.feature h3{margin-top:22px;font-size:20px;font-weight:600;color:var(--blue)}
.feature p{margin-top:10px;font-size:16.5px;line-height:1.25;color:var(--grey)}
.arrow{position:absolute;top:283px}

/* cta band */
.cta-band{top:1987px;height:134px;background:var(--blue);color:var(--white);font-family:"Exo 2",sans-serif}
.quote{position:absolute;left:104px;top:24px}
.quote-label{font-size:28px;font-weight:600}
.quote-number{font-size:40px;font-weight:600;line-height:1.15}
.band-divider{position:absolute;left:407px;top:30px;height:80px;border-left:2px dotted rgba(255,255,255,.7)}
.newsletter-title{position:absolute;left:466px;top:20px;font-size:28px;font-weight:600}
.newsletter{position:absolute;left:466px;top:64px;display:flex;gap:12px}
.field{height:46px;background:var(--white);color:#999;font-family:"Open Sans",sans-serif;font-size:14px;padding:13px 12px}
.field-name{width:272px}
.field-email{width:273px}
.go{width:56px;height:46px;background:var(--green);font-size:22px;font-weight:700;display:flex;align-items:center;justify-content:center}

/* footer */
.site-footer{top:2121px;height:358px;background:var(--footer);color:var(--white);font-family:"Open Sans",sans-serif}
.col{position:absolute;top:56px}
.col h4{font-family:"Raleway",sans-serif;font-size:15px;font-weight:700;margin-bottom:22px;line-height:20px}
.col-about{left:104px;width:200px;font-size:12px;line-height:1.6}
.col-services{left:362px;font-size:12px;line-height:25.5px}
.col-hours{left:602px;font-size:12px;line-height:30px}
.col-touch{left:876px}
.socials{display:flex;gap:8px;margin-top:16px}
.socials span{width:28px;height:28px;border:1px solid #444;display:block}
.contact-row{display:flex;gap:12px;margin-bottom:22px;font-size:11.5px;line-height:1.45}
.contact-icon{width:38px;height:38px;border:1px solid #bbb;display:flex;align-items:center;justify-content:center;flex:none}
.contact-row b{font-size:11.5px;font-weight:600}
.footer-rule{position:absolute;left:104px;top:287px;width:997px;border-top:1px solid var(--rule)}
.copyright{position:absolute;left:0;width:1200px;top:304px;text-align:center;font-size:12px}
</style>
</head>
<body>

<header class="block site-header">
  <div class="brand"><span class="brand-mark"></span><span class="brand-name">Halt &amp; Fullmane</span></div>
  <div class="brand-by">by Robert Pembrook M.D.</div>
  <div class="call">
    <svg width="30" height="30" viewBox="0 0 24 24" fill="none" stroke="#aaa" stroke-width="1.4"><path d="M5 3h4l2 5-3 2a11 11 0 0 0 6 6l2-3 5 2v4a2 2 0 0 1-2 2A17 17 0 0 1 3 5a2 2 0 0 1 2-2z"/></svg>
    <div><div class="call-label">CALL US</div><div class="call-number">(310) 555-0147</div></div>
  </div>
  <a class="btn header-cta" href="#">BOOK APPOINTMENT</a>
</header>

<nav class="block main-nav">
  <ul>
    <li><a href="#">Home</a></li><li><a href="#">About Us</a></li><li><a href="#">How It Works</a></li>
    <li><a href="#">Success Stories</a></li><li><a href="#">Faqs</a></li><li><a href="#">Blog</a></li>
    <li><a href="#">Salon Partners</a></li><li><a href="#">Book Now</a></li><li><a href="#">Contact</a></li>
  </ul>
  <div class="nav-search"><svg width="18" height="18" viewBox="0 0 24 24" fill="none" stroke="#fff" stroke-width="2.4"><circle cx="10" cy="10" r="7"/><path d="M15 15l6 6"/></svg></div>
</nav>

<section class="block hero">
  <div class="hero-photo" role="img" aria-label="Photo of a young man in a white vest checking his hairline with both hands"></div>
  <h1 class="hero-title">Stop Hereditary Hair Loss And Regrow a Full, Healthy Head of Hair</h1>
  <p class="hero-text">Halt and Fullmane uses a scientific approach to preventing hair loss and regrowing your hair.</p>
  <div class="hero-actions"><a class="btn btn-blue" href="#">Get Appointment</a><a class="btn btn-green" href="#">Contact Us</a></div>
</section>

<section class="block about">
  <h2 class="section-title">ABOUT US</h2>
  <h3 class="about-sub">Dr Pembrook story – why he created this solution</h3>
  <p class="about-text">Dr. Robert Pembrook, the creator of Halt and Fullmane is a renowned hair restoration expert. After seeing first his father and then older brothers thin and go bald, he dedicated his life to finding the cure for hair loss. After initially pioneering the single hair method for hair transplant, he determined there must be a non-surgical solution and spent the last 20 years in research and clinical trial and error first creating, then perfecting what is now the Halt and Fullmane solution for hair loss.</p>
  <a class="btn" href="#">Read More</a>
  <div class="about-video" role="img" aria-label="Video still of a man examining his thinning hair in a mirror">
    <svg class="play" width="66" height="66" viewBox="0 0 66 66"><circle cx="33" cy="33" r="31" fill="rgba(255,255,255,.25)" stroke="#fff" stroke-width="3"/><path d="M26 20l20 13-20 13z" fill="#fff"/></svg>
  </div>
</section>

<section class="block how">
  <div class="how-photo" role="img" aria-label="Photo of a barber trimming a seated client's hair in a salon"></div>
  <div class="how-panel">
    <h2 class="section-title">HOW IT WORKS</h2>
    <h3 class="how-sub">The science behind the effectiveness of<br>Halt &amp; Fullmane™</h3>
    <div class="how-text">
      <p>Halt and Fullmane uses a scientific approach to preventing hair loss and regrowing your hair. The first thing we will do in your consultation is determine your specific cause of hair loss in order to create you a personalized program to first stop the hair loss then regrow it. Your cause could be hereditary, hormonal, stress related, diet, medication induced or a combination of some or all of these.</p>
      <p>The vast majority of cases we see do have at least some component of hereditary baldness as part of the mix. The reason it is hereditary is due to a small defect on</p>
    </div>
    <div class="how-more">Read More</div>
  </div>
</section>

<section class="block why">
  <h2 class="why-title">WHY OUR HAIR RECOVERY CLINIC IS THE BEST?</h2>
  <svg class="arrow" style="left:73px" width="12" height="18" viewBox="0 0 12 18" fill="none" stroke="#555" stroke-width="1.6"><path d="M10 2L3 9l7 7"/></svg>
  <svg class="arrow" style="left:1117px" width="12" height="18" viewBox="0 0 12 18" fill="none" stroke="#555" stroke-width="1.6"><path d="M2 2l7 7-7 7"/></svg>
  <div class="features">
    <article class="feature">
      <div class="feature-photo" role="img" aria-label="Photo of a smiling man running a hand through his hair"></div>
      <h3>NO SIDE EFFECTS</h3>
      <p>All ingredients are FDA approved<br>and safe</p>
    </article>
    <article class="feature">
      <div class="feature-photo" role="img" aria-label="Photo of a specialist marking a patient's hairline with a pen"></div>
      <h3>THE ACTIVE INGREDIENTS</h3>
      <p>Purely Core ingredients – no harsh<br>preservatives or chemicals<br>are included</p>
    </article>
    <article class="feature">
      <div class="feature-photo" role="img" aria-label="Photo of a man in a white vest checking his scalp"></div>
      <h3>MONEY BACK</h3>
      <p>Money back guaranteed results</p>
    </article>
  </div>
</section>

<section class="block cta-band">
  <div class="quote"><div class="quote-label">GET A QUOTE</div><div class="quote-number">(310) 555-0147</div></div>
  <div class="band-divider"></div>
  <h2 class="newsletter-title">SUBSCRIBE TO NEWSLETTER</h2>
  <div class="newsletter">
    <div class="field field-name">Your Name</div>
    <div class="field field-email">Type Your Email</div>
    <div class="go">GO</div>
  </div>
</section>

<footer class="block site-footer">
  <div class="col col-about">
    <h4>About Us</h4>
    <p>Lorem Ipsum has been the industry's standard dummy text ever since the 1500s, when an unknown printer took a galley of type and scrambled it to make a type specimen book.</p>
    <div class="socials"><span></span><span></span><span></span><span></span></div>
  </div>
  <div class="col col-services">
    <h4>Services</h4>
    <p>Cosmetic Dentistry<br>Advanced Technology<br>Mini Planet<br>Preventive Dentistry<br>Genral Dentistry<br>Emergency Dentistry</p>
  </div>
  <div class="col col-hours">
    <h4>Office Hours</h4>
    <p>Monday : 0900 - 17:00<br>Tuesday : : 0900 - 17:00<br>Wednesday: : 0900 - 17:00<br>Thursday : : 0900 - 17:00<br>Friday: : 0900 - 17:00<br>Saturday: : 0800 - 14:00</p>
  </div>
  <div class="col col-touch">
    <h4>Get in Touch</h4>
    <div class="contact-row">
      <span class="contact-icon"><svg width="14" height="14" viewBox="0 0 24 24" fill="#fff"><path d="M12 3l10 9h-3v9h-5v-6h-4v6H5v-9H2z"/></svg></span>
      <div><b>ADDRESS:</b><br>2180 Linden Ave, Suite 410<br>Westmere CA 90000</div>
    </div>
    <div class="contact-row">
      <span class="contact-icon"><svg width="10" height="16" viewBox="0 0 10 16" fill="none" stroke="#fff" stroke-width="1.6"><rect x="1" y="1" width="8" height="14" rx="1.5"/></svg></span>
      <div><b>PHONE:</b><br>(310) 555-0147</div>
    </div>
    <div class="contact-row">
      <span class="contact-icon"><svg width="16" height="12" viewBox="0 0 16 12" fill="#fff"><path d="M0 0h16v12H0z"/><path d="M0 0l8 6 8-6" fill="none" stroke="#262626" stroke-width="1.4"/></svg></span>
      <div><b>EMAIL:</b><br>support@haltandfullmane.example</div>
    </div>
  </div>
  <div class="footer-rule"></div>
  <p class="copyright">haltandfullmane. All Rights Reserved.2017</p>
</footer>

</body>
</html>
```